Harborlight Amusement Collective (HAC)

We need a business card design for Harborlight Amusement Collective. Modern and sleek looking, with all critical information. Open to single or double sided designs, if double sided info needs to be all on one side. The main Logo is Harborlight Amusement collective and must be on the card. The other three logos are for the brands that fall under the group, they might be good on the back.

Industry/Entity Type

Business

```html
<!DOCTYPE html>
<html lang="en">
<head>
<meta charset="utf-8">
<title>Harborlight Amusement Collective – Business Card</title>
<link href="https://fonts.googleapis.com/css2?family=Montserrat:wght@400;500;600;700;800&family=Encode+Sans+Condensed:wght@700&display=swap" rel="stylesheet">
<style>
  :root {
    --blue: #2a4f9e;
    --green: #8aa631;
    --ink: #333a40;
    --muted: #6b7278;
    --card: #ffffff;
    --stage: #e4e4e4;
    --rule: #d6d9dc;
  }
  * { box-sizing: border-box; margin: 0; padding: 0; }
  html, body {
    width: 1200px; height: 852px; overflow: hidden;
    background: var(--stage);
    font-family: "Montserrat", Arial, sans-serif;
    color: var(--ink);
  }
  .stage {
    width: 1200px; height: 852px;
    display: flex; align-items: center; justify-content: center; gap: 40px;
  }
  .card {
    position: relative;
    width: 540px; height: 310px;
    background: var(--card);
    border-radius: 24px;
    box-shadow: 0 6px 18px rgba(0,0,0,.18);
    overflow: hidden;
  }

  /* Wordmark */
  .wordmark { display: flex; align-items: center; gap: 12px; }
  .wordmark-square { width: 34px; height: 34px; background: var(--blue); flex: none; }
  .wordmark-name {
    font-weight: 700; color: var(--blue);
    text-transform: uppercase; letter-spacing: .04em; line-height: 1.15;
  }

  /* Front */
  .front { display: flex; flex-direction: column; align-items: center; }
  .front .wordmark { margin-top: 48px; }
  .front .wordmark-name { font-size: 19px; }
  .front .wordmark-square { width: 44px; height: 44px; }
  .front-rule { width: 380px; height: 2px; background: var(--blue); margin-top: 16px; }
  .brands-label {
    margin-top: 18px; font-size: 12px; color: var(--ink); letter-spacing: .03em;
  }
  .brands-rule { width: 460px; height: 1.5px; background: var(--green); margin-top: 8px; }
  .brand-row {
    margin-top: 20px; display: flex; align-items: center;
  }
  .brand {
    display: flex; align-items: center; gap: 7px;
    padding: 0 20px; font-size: 17px; font-weight: 700; color: var(--blue);
  }
  .brand + .brand { border-left: 1.5px solid var(--rule); }
  .brand-dot { width: 16px; height: 16px; border-radius: 50%; background: var(--green); }
  .website { margin-top: 22px; font-size: 12.5px; color: var(--ink); }
  .website span { color: var(--blue); }
  .website-rule { width: 300px; height: 1.5px; background: var(--green); margin-top: 10px; }

  /* Back */
  .back .wordmark {
    position: absolute; top: 52px; right: 34px; flex-direction: column; align-items: center; gap: 8px;
  }
  .back .wordmark-name { font-size: 14px; text-align: center; }
  .back-logo-rule { width: 200px; height: 2px; background: var(--blue); }
  .address {
    position: absolute; top: 156px; right: 34px;
    font-size: 12px; text-align: right; line-height: 1.5; color: var(--ink);
  }
  .accent-dot {
    position: absolute; left: -30px; top: 200px;
    width: 60px; height: 60px; border-radius: 50%; background: var(--green);
  }
  .person { position: absolute; left: 50px; top: 166px; }
  .person-line { display: flex; align-items: flex-end; gap: 12px; }
  .person-name {
    font-family: "Encode Sans Condensed", "Arial Narrow", sans-serif;
    font-size: 23px; color: var(--blue); line-height: 1;
  }
  .name-rule { width: 100px; height: 1.5px; background: var(--green); margin-bottom: 5px; }
  .person-title { font-size: 12.5px; margin-top: 4px; }
  .contacts { list-style: none; margin-top: 14px; font-size: 12.5px; }
  .contacts li { display: flex; align-items: center; gap: 12px; height: 21px; }
  .contacts svg { width: 13px; height: 13px; fill: var(--blue); flex: none; }
  .contacts .accent { color: var(--blue); }
</style>
</head>
<body>
<main class="stage">

  <section class="card front" aria-label="Card front">
    <div class="wordmark">
      <span class="wordmark-square"></span>
      <span class="wordmark-name">Harborlight Amusement<br>Collective</span>
    </div>
    <div class="front-rule"></div>
    <p class="brands-label">Our Brands</p>
    <div class="brands-rule"></div>
    <div class="brand-row">
      <span class="brand"><span class="brand-dot"></span>HarborPass</span>
      <span class="brand"><span class="brand-dot"></span>Boxseat Hosting</span>
      <span class="brand"><span class="brand-dot"></span>Gatemark</span>
    </div>
    <p class="website">www.<span>harborlightcollective</span>.com</p>
    <div class="website-rule"></div>
  </section>

  <section class="card back" aria-label="Card back">
    <div class="wordmark">
      <span class="wordmark-square"></span>
      <span class="wordmark-name">Harborlight Amusement<br>Collective</span>
      <span class="back-logo-rule"></span>
    </div>
    <p class="address">234 Anywhere St., Any<br>City Town, US 123456</p>
    <span class="accent-dot"></span>
    <div class="person">
      <div class="person-line">
        <h1 class="person-name">Avery Lane Brooks</h1>
        <span class="name-rule"></span>
      </div>
      <p class="person-title">Managing Director</p>
      <ul class="contacts">
        <li>
          <svg viewBox="0 0 16 16" aria-hidden="true"><path d="M3.6 1.5l2.3 2.6-1.3 1.8c.9 2 2.5 3.6 4.5 4.5l1.8-1.3 2.6 2.3-1.2 2.2C7.2 13.7 2.3 8.8 1.4 3.7z"/></svg>
          <span>555.555.5555</span>
        </li>
        <li>
          <svg viewBox="0 0 16 16" aria-hidden="true"><path d="M1 3h14v10H1zM2.5 4.5 8 9l5.5-4.5z" fill-rule="evenodd"/></svg>
          <span>averybrooks@yourwebsite.com</span>
        </li>
        <li>
          <svg viewBox="0 0 16 16" aria-hidden="true"><circle cx="8" cy="8" r="6.5" fill="none" stroke="#2a4f9e" stroke-width="1.5"/><path d="M1.5 8h13M8 1.5v13" stroke="#2a4f9e" stroke-width="1.2"/></svg>
          <span>www.<span class="accent">yourwebsite</span>.com</span>
        </li>
      </ul>
    </div>
  </section>

</main>
</body>
</html>
```